Business Card & Email Signature Design || Upmarket + Luxury

Rima Vale Honey, a New Zealand Manuka Honey company needs a Business Card & Email Signature design.

Our logo's are attached in Gold & Black versions, feel free to be creative with how you use the logo and it's patterns in your design.

Style:
- Looking for an Elegant, Luxurious, Upmarket feel.
- Black/Matte Black Card, Gold Foil, UV Embossing

Information to Add:

- Logo
- Company Name: Rima Vale Honey
- Name: Martin Holloway
- Title: Creative Director
- Phone: +64 2815 96 417
- Email: martin@rimavalehoney.example.nz
- Website: www.rimavalehoney.example.nz

- Socials: ***For email Signature Only***
- Facebook: https://www.facebook.com/rimavalehoney/
- Instagram: https://www.instagram.com/rimavalehoney/

Target Market(s)

Asia/Europe Luxury, Upmarket

Contact Information for Business Card

- Logo
- Name: Martin Holloway
- Phone: +64 2815 96 417

Font styles to use
Other font styles liked:
• Champagne & Limousines (Attached)

Requirements
Must have
• Business Card & Email Signature Design.

Looking for a Sleek, Luxury, Upmarket Design.

```html
<!DOCTYPE html>
<html lang="en">
<head>
<meta charset="utf-8">
<title>Rima Vale Honey – Business Card</title>
<link href="https://fonts.googleapis.com/css2?family=Montserrat:wght@400;600&display=swap" rel="stylesheet">
<style>
  :root {
    --backdrop: #aaaba6;
    --card: #1d1d1d;
    --card-edge: #c7c46a;
    --gold: #c9a45e;
    --gold-light: #dcbd7a;
  }
  * { margin: 0; padding: 0; box-sizing: border-box; }
  html, body {
    width: 1200px; height: 801px; overflow: hidden;
    background: var(--backdrop);
    font-family: "Montserrat", Arial, sans-serif;
  }
  .stage {
    position: relative; width: 1200px; height: 801px;
    display: flex; align-items: center; justify-content: center; gap: 44px;
  }
  .card {
    position: relative; width: 540px; height: 309px;
    background: var(--card);
    border-bottom: 3px solid var(--card-edge);
    box-shadow: 0 14px 30px rgba(0,0,0,0.28);
    color: var(--gold);
  }
  /* front */
  .card-front .person {
    position: absolute; left: 40px; top: 128px; width: 220px;
  }
  .person-name {
    font-weight: 600; font-size: 18px; letter-spacing: 0.05em;
    color: var(--gold-light); text-transform: uppercase; white-space: nowrap;
  }
  .person-title {
    font-size: 11.5px; margin-top: 3px; letter-spacing: 0.02em;
  }
  .contact-list {
    position: absolute; left: 40px; bottom: 30px; list-style: none;
    font-size: 10.5px; line-height: 1.75; letter-spacing: 0.02em;
  }
  .contact-list li { display: flex; align-items: center; gap: 8px; white-space: nowrap; }
  .contact-list svg { width: 11px; height: 11px; flex: none; }
  .front-brand {
    position: absolute; left: 275px; top: 22px; width: 245px; height: 250px;
    display: flex; flex-direction: column; align-items: center; justify-content: center; gap: 20px;
  }
  .brand-dot {
    width: 14px; height: 14px; border-radius: 50%;
    border: 1.5px solid var(--gold);
  }
  .front-brand .brand-dot { width: 150px; height: 150px; border-width: 2px; }
  .brand-name {
    font-weight: 400; color: var(--gold); text-transform: uppercase;
    letter-spacing: 0.18em; font-size: 15px; white-space: nowrap;
  }
  /* back */
  .card-back {
    display: flex; flex-direction: column; align-items: center; justify-content: center; gap: 22px;
  }
  .card-back .brand-dot { width: 26px; height: 26px; border-width: 2px; }
  .card-back .brand-name { font-size: 27px; letter-spacing: 0.16em; }
</style>
</head>
<body>
<main class="stage">
  <section class="card card-front" aria-label="Business card front">
    <div class="person">
      <p class="person-name">Martin Holloway</p>
      <p class="person-title">Creative Director</p>
    </div>
    <ul class="contact-list">
      <li>
        <svg viewBox="0 0 12 12" aria-hidden="true"><path d="M3 1 L5 3.5 L4 5 Q5 7 7 8 L8.5 7 L11 9 L10 11 Q4 11 1 2 Z" fill="none" stroke="currentColor" stroke-width="1"/></svg>
        +64 2815 96 417
      </li>
      <li>
        <svg viewBox="0 0 12 12" aria-hidden="true"><rect x="1" y="2.5" width="10" height="7" fill="none" stroke="currentColor"/><path d="M1 2.5 L6 6.5 L11 2.5" fill="none" stroke="currentColor"/></svg>
        martin@rimavalehoney.example.nz
      </li>
      <li>
        <svg viewBox="0 0 12 12" aria-hidden="true"><circle cx="6" cy="6" r="5" fill="none" stroke="currentColor"/><ellipse cx="6" cy="6" rx="2.2" ry="5" fill="none" stroke="currentColor"/><path d="M1 6 H11" stroke="currentColor"/></svg>
        www.rimavalehoney.example.nz
      </li>
    </ul>
    <div class="front-brand">
      <span class="brand-dot" aria-hidden="true"></span>
      <span class="brand-name">Rima Vale Honey</span>
    </div>
  </section>

  <section class="card card-back" aria-label="Business card back">
    <span class="brand-dot" aria-hidden="true"></span>
    <span class="brand-name">Rima Vale Honey</span>
  </section>
</main>
</body>
</html>
```